Defense Attorney Business Card Design Project/ Stationary

I am looking for a distinctive business card design for my solo law practice.
I practice criminal defense, both juvenile and adult, including DUI. I am a very experienced attorney with prior military experience. The design should convey a traditional, old school flair, but not be too stodgy or uptight. Some color. My logo should appear.
Updates

Project Deadline Extended Reason: I misunderstood how this project works and I was not prepared with my logo when this project ran the first time. Added Thursday, November 13, 2014

Project Deadline Extended
Reason: I was sent overseas on military duty last year, which interrupted this project. Thank you for your participation... I hope we can get this done this week! Thank you, Neil

Target Market(s)

Regular everyday people looking for strong, knowledgeable, authoritative representation while they are faced with criminal charges. Many have never been charged with a crime before. A reassuring air is therefore desired.

Industry/Entity Type

Business

Contact Information for Business Card

My information is:
Theodore M. Quill, Attorney at Law
785 Birch Avenue Suite 300
Oakland, California 94719
Tel: (510) 384-6125
Fax: (510) 391-7802
email: neilquilllaw@mailvine.example
web: www.neilquilllaw.example

Font styles to use
Serif
Sans Serif
Decorative

Colors
0255a3
ffffff

Requirements
Must have
• Sharp lines, bold elements. Conservative use of colors, such as deep blues, burgundy, grays for example.
• While my logo says "Neil Quill", it should be modified to show "Theodore M. Quill".
Should not have
• Cliche imagery such as scales of justice, gavels, Statue of Liberty, etc.

```html
<!DOCTYPE html>
<html lang="en">
<head>
<meta charset="utf-8">
<title>Theodore M. Quill – Business Card</title>
<link href="https://fonts.googleapis.com/css2?family=Cinzel:wght@400;600&display=swap" rel="stylesheet">
<style>
  :root {
    --backdrop: #e7e9eb;
    --card-light: #ffffff;
    --card-shade: #e4e6e8;
    --band: #1d4d69;
    --silver-dark: #6f767b;
    --ink: #1c4a66;
    --on-band: #ffffff;
  }
  html, body {
    margin: 0;
    width: 1200px;
    height: 899px;
    overflow: hidden;
    background: var(--backdrop);
  }
  .card {
    position: absolute;
    left: 180px;
    top: 210px;
    width: 840px;
    height: 480px;
    border-radius: 44px;
    overflow: hidden;
    background: linear-gradient(180deg, var(--card-light) 0%, var(--card-shade) 60%);
    box-shadow: 0 14px 40px rgba(0,0,0,0.18);
    font-family: "Cinzel", serif;
  }
  .card-wave {
    position: absolute;
    inset: 0;
  }
  .brand {
    position: absolute;
    left: 0;
    right: 0;
    top: 92px;
    text-align: center;
    color: var(--ink);
  }
  .brand-name {
    font-size: 42px;
    font-weight: 600;
    letter-spacing: 2px;
    line-height: 1;
  }
  .brand-tagline {
    display: inline-block;
    margin-top: 10px;
    padding: 5px 14px 3px;
    border-top: 2px solid var(--ink);
    border-bottom: 2px solid var(--ink);
    font-size: 19px;
    font-weight: 600;
    letter-spacing: 3px;
  }
  .person {
    position: absolute;
    right: 500px;
    top: 300px;
    text-align: right;
    color: var(--on-band);
    font-size: 16px;
    line-height: 1.45;
    letter-spacing: 1px;
    white-space: nowrap;
  }
  .person-name { font-weight: 600; font-size: 18px; }
  .person-title { margin-bottom: 14px; }
  .divider {
    position: absolute;
    left: 358px;
    top: 296px;
    width: 2px;
    height: 128px;
    background: var(--on-band);
  }
  .contacts {
    position: absolute;
    left: 376px;
    top: 298px;
    margin: 0;
    padding: 0;
    list-style: none;
    color: var(--on-band);
    font-size: 16px;
    letter-spacing: 1px;
    white-space: nowrap;
  }
  .contacts li {
    display: flex;
    align-items: center;
    height: 30px;
  }
  .contacts svg {
    width: 18px;
    height: 18px;
    margin-right: 9px;
    flex: none;
  }
</style>
</head>
<body>
  <div class="card">
    <svg class="card-wave" viewBox="0 0 840 480" preserveAspectRatio="none" aria-hidden="true">
      <defs>
        <linearGradient id="silverEdge" x1="0" y1="0" x2="1" y2="0">
          <stop offset="0" stop-color="#8c9397"/>
          <stop offset="0.5" stop-color="#e9ecee"/>
          <stop offset="1" stop-color="#7c8489"/>
        </linearGradient>
        <linearGradient id="bandFill" x1="0" y1="0" x2="0" y2="1">
          <stop offset="0" stop-color="#22587a"/>
          <stop offset="1" stop-color="#173f57"/>
        </linearGradient>
      </defs>
      <path d="M0,246 C260,286 540,292 840,176 L840,206 C540,318 260,308 0,276 Z" fill="url(#silverEdge)"/>
      <path d="M0,274 C260,306 540,316 840,200 L840,480 L0,480 Z" fill="var(--silver-dark)"/>
      <path d="M0,282 C260,314 540,324 840,208 L840,480 L0,480 Z" fill="url(#bandFill)"/>
    </svg>

    <div class="brand">
      <div class="brand-name">Theodore M. Quill</div>
      <div class="brand-tagline">Attorney at Law</div>
    </div>

    <div class="person">
      <div class="person-name">Theodore M. Quill</div>
      <div class="person-title">Attorney at Law</div>
      <div>785 Birch Avenue Suite 300,</div>
      <div>Oakland, CA 94719</div>
    </div>

    <div class="divider"></div>

    <ul class="contacts">
      <li>
        <svg viewBox="0 0 18 18" aria-hidden="true"><circle cx="9" cy="9" r="9" fill="#fff"/><path d="M5.5 4.5l2 .3.6 2.2-1.1.8a6 6 0 0 0 3.2 3.2l.8-1.1 2.2.6.3 2c-3.8.8-8.8-4.2-8-8z" fill="var(--band)"/></svg>
        Tel: (510) 384-6125
      </li>
      <li>
        <svg viewBox="0 0 18 18" aria-hidden="true"><circle cx="9" cy="9" r="9" fill="#fff"/><rect x="4.5" y="7" width="9" height="6" rx="1" fill="var(--band)"/><rect x="6.5" y="4" width="5" height="4" fill="var(--band)"/></svg>
        Fax: (510) 391-7802
      </li>
      <li>
        <svg viewBox="0 0 18 18" aria-hidden="true"><circle cx="9" cy="9" r="9" fill="#fff"/><rect x="4" y="5.5" width="10" height="7" rx="1" fill="var(--band)"/><path d="M4.5 6l4.5 3.5L13.5 6" stroke="#fff" stroke-width="1" fill="none"/></svg>
        neilquilllaw@mailvine.example
      </li>
      <li>
        <svg viewBox="0 0 18 18" aria-hidden="true"><circle cx="9" cy="9" r="9" fill="#fff"/><circle cx="9" cy="9" r="5" fill="none" stroke="var(--band)" stroke-width="1.3"/><path d="M4 9h10M9 4c-2.5 3-2.5 7 0 10M9 4c2.5 3 2.5 7 0 10" stroke="var(--band)" stroke-width="1" fill="none"/></svg>
        www.neilquilllaw.example
      </li>
    </ul>
  </div>
</body>
</html>
```